SUPPLEMENT BOTTLE LABEL: TOLVERIN

We need a NEW FRESH look to her labels. Something contemporary, clean and professional. The colors need to remain the same but everything else can change, even the logo.

THE CURRENT LABEL IS ATTACHED IN PDF FORMAT

Target Market(s)

WOMEN BETWEEN 35-60

Requirements
Must have
• SAME COLORS
• FRESH
• CLEAN

```html
<!DOCTYPE html>
<html lang="en">
<head>
<meta charset="UTF-8">
<title>Balanced Renew – Cleanse Chocolate Label</title>
<link rel="stylesheet" href="https://fonts.googleapis.com/css2?family=Kaushan+Script&family=Squada+One&family=Mali:wght@600;700&display=swap">
<style>
  :root {
    --backdrop: #b3aac3;
    --sky-light: #14d0f8;
    --sky-mid: #1fb4ec;
    --sky-deep: #1a8fe0;
    --navy: #1f3f9c;
    --navy-deep: #1a34a0;
    --navy-edge: #2453b8;
    --white: #ffffff;
    --ink-shadow: rgba(10, 40, 90, 0.35);
  }
  * { margin: 0; padding: 0; box-sizing: border-box; }
  html, body {
    width: 1200px;
    height: 1200px;
    overflow: hidden;
    background: var(--backdrop);
  }
  .canvas {
    position: relative;
    width: 1200px;
    height: 1200px;
    display: flex;
    align-items: center;
    justify-content: center;
  }
  .label {
    width: 920px;
    height: 1080px;
    display: flex;
    flex-direction: column;
    color: var(--white);
    text-align: center;
  }
  .label-top {
    flex: 0 0 650px;
    background: linear-gradient(100deg, var(--sky-deep) 0%, var(--sky-mid) 35%, var(--sky-light) 65%, var(--sky-mid) 100%);
    display: flex;
    flex-direction: column;
    align-items: center;
    justify-content: flex-end;
    padding-bottom: 50px;
  }
  .brand-name {
    font-family: "Kaushan Script", cursive;
    font-size: 124px;
    line-height: 1;
    margin-bottom: 30px;
  }
  .product-name {
    font-family: "Squada One", sans-serif;
    font-size: 120px;
    line-height: 0.95;
    letter-spacing: 4px;
    color: var(--white);
    -webkit-text-stroke: 3px var(--sky-deep);
    text-shadow: 4px 4px 0 var(--ink-shadow);
  }
  .flavor-note {
    font-family: "Mali", sans-serif;
    font-weight: 700;
    font-size: 40px;
    margin-top: 14px;
  }
  .label-bottom {
    flex: 1;
    background: linear-gradient(180deg, var(--navy) 0%, var(--navy-deep) 88%, var(--navy-edge) 100%);
    display: flex;
    flex-direction: column;
    align-items: center;
    padding-top: 42px;
    font-family: "Mali", sans-serif;
    font-weight: 600;
  }
  .supplement-type {
    font-size: 33px;
    line-height: 1.5;
  }
  .usage-notice {
    font-size: 33px;
    line-height: 1.45;
  }
  .net-weight {
    display: flex;
    align-items: center;
    gap: 8px;
    margin-top: 52px;
    font-size: 32px;
    font-weight: 700;
  }
  .net-weight .rule {
    width: 70px;
    height: 2px;
    background: var(--white);
  }
</style>
</head>
<body>
  <main class="canvas">
    <section class="label">
      <div class="label-top">
        <h1 class="brand-name">Balanced Renew</h1>
        <h2 class="product-name">CLEANSE<br>CHOCOLATE</h2>
        <p class="flavor-note">with other natural flavors</p>
      </div>
      <div class="label-bottom">
        <p class="supplement-type">Collagen, Multivitamin, Mineral &amp;<br>Herbal Dietary Supplement Powder</p>
        <p class="usage-notice">Notice: Use this product as a food supplement only.<br>Do not use for weight reduction.</p>
        <p class="net-weight"><span class="rule"></span>NET WT. 1.21 LBS (551.2 G)<span class="rule"></span></p>
      </div>
    </section>
  </main>
</body>
</html>
```